Investment firm needs refreshed corporate powerpoint slides design

We need a new and refreshed powerpoint template for our corporate investment deck. We are a technology private equity group that primarily invests in fast growing software companies and we would like to reflect that in a modern and light blue / transparant / white powerpoint and fonts template. I have also attached our old investor deck as a guideline and also check out our website to get an idea of what we do and what type of companies we invested in. Please note that our website is old and so our presentation should be a refreshed "2017" modern design, not a copy / paste of our website design and graphics.
Updates

Project Deadline Extended Reason: I'm extending the deadline to February 27, but we would ideally receive something by the end of this week.Please submit updates. Thanks Added Tuesday, February 21, 2017

Target Market(s)

Investors such as high net worth individuals, pension funds, banks, financial advisors

Industry/Entity Type

Investment

Colors
33a6d7
85cae6
cfeae6
edf8f6
ffffff
fff3d1
86cfc6

Requirements
Must have
• We let you be creative, we trust you have seen more investment presentations before.
Nice to have
• Pre-built models, flow charts, graphs, charts, etc.
Should not have
• Fancy or edgy images, this has to be a modern, fresh and trustworthy looking powerpoint template. No stock images, if you do use stock images for background purposes please be creative! :-)

```html
<!DOCTYPE html>
<html lang="en">
<head>
<meta charset="utf-8">
<title>Alderfield corporate deck slides</title>
<link href="https://fonts.googleapis.com/css2?family=Raleway:wght@400;500;600;700&display=swap" rel="stylesheet">
<style>
:root{
  --navy:#1d4e7c; --deep:#0f2d5a; --blue:#7ab8d8; --sky:#85cae6; --bright:#33a6d7;
  --teal:#86cfc6; --mint:#cfeae6; --ice:#edf8f6; --white:#ffffff; --grey:#a9acaf; --text:#8c9399;
}
*{box-sizing:border-box;margin:0;padding:0}
html,body{width:1096px;height:1200px;overflow:hidden;background:#f3f4f5;font-family:'Raleway',sans-serif}
.deck{position:relative;width:1096px;height:1200px}
.slide{position:absolute;width:342px;height:192px;background:var(--white);overflow:hidden;box-shadow:0 1px 4px rgba(0,0,0,.18)}
.c1{left:11px}.c2{left:376px}.c3{left:740px}
.r1{top:6px}.r2{top:203px}.r3{top:401px}.r4{top:598px}.r5{top:796px}.r6{top:994px}
.abs{position:absolute}
.marker{position:absolute;left:0;top:13px;width:0;height:0;border-top:6px solid transparent;border-bottom:6px solid transparent;border-left:6px solid #cfd3d6}
.title{position:absolute;left:14px;top:10px;font-size:15px;font-weight:700;color:var(--navy);white-space:nowrap}
.title.ul::after{content:"";position:absolute;left:0;top:21px;width:22px;height:2px;background:var(--teal)}
.brand{position:absolute;right:12px;top:9px;font-size:15px;font-weight:500;color:var(--navy);display:flex;align-items:center;gap:4px}
.brand::before{content:"";width:4px;height:4px;background:#b5bcc2}
.foot{position:absolute;left:0;right:0;bottom:0;height:12px;background:var(--blue);font-size:4px;color:#fff;line-height:12px;padding-left:4px}
.foot b{position:absolute;right:0;top:0;width:14px;height:12px;background:var(--teal);text-align:center;font-weight:500}
.tiny{font-size:4.3px;line-height:5.5px;color:var(--text)}
.small{font-size:5.5px;line-height:7px;color:var(--text)}
.lbl{font-size:6px;font-weight:600;color:var(--navy)}
.ph{position:absolute;background:linear-gradient(135deg,#c9d3db,#7d8c99)}
.circle{border-radius:50%}
</style>
</head>
<body>
<div class="deck">

<!-- Line chart area -->
<section class="slide c1 r1">
  <span class="marker"></span><h2 class="title">Your Line Chart Area</h2><div class="brand">Alderfield</div>
  <div class="abs small" style="left:72px;top:59px;font-size:5.5px;color:#555">Chart Title</div>
  <div class="abs small" style="left:232px;top:59px;font-size:5.5px;color:#555">Chart Title</div>
  <svg class="abs" style="left:30px;top:68px" width="290" height="70" viewBox="0 0 290 70">
    <g stroke="#eee" stroke-width=".5"><line x1="10" y1="5" x2="120" y2="5"/><line x1="10" y1="20" x2="120" y2="20"/><line x1="10" y1="35" x2="120" y2="35"/><line x1="10" y1="50" x2="120" y2="50"/><line x1="10" y1="65" x2="120" y2="65"/>
    <line x1="170" y1="5" x2="280" y2="5"/><line x1="170" y1="20" x2="280" y2="20"/><line x1="170" y1="35" x2="280" y2="35"/><line x1="170" y1="50" x2="280" y2="50"/><line x1="170" y1="65" x2="280" y2="65"/></g>
    <polyline points="14,60 30,38 48,10 66,55 84,8 102,42 118,18" fill="none" stroke="var(--teal)" stroke-width="1"/>
    <polyline points="14,38 30,28 48,35 66,45 84,28 102,38 118,30" fill="none" stroke="var(--bright)" stroke-width="1"/>
    <polyline points="176,50 196,20 214,45 234,15 256,40 278,25" fill="none" stroke="var(--teal)" stroke-width="1"/>
    <polyline points="176,40 196,30 214,25 234,40 256,28 278,35" fill="none" stroke="var(--bright)" stroke-width="1"/>
    <g font-size="4" fill="#999"><text x="0" y="7">70</text><text x="0" y="37">40</text><text x="0" y="67">0</text><text x="160" y="7">70</text><text x="160" y="37">40</text><text x="160" y="67">0</text></g>
  </svg>
  <p class="abs tiny" style="left:36px;top:142px;width:120px">Lorem ipsum dolor sit amet, consectetur adipiscing elit sed diam nonummy nibh euismod tincidunt ut laoreet.</p>
  <p class="abs tiny" style="left:196px;top:142px;width:120px">Lorem ipsum dolor sit amet, consectetur adipiscing elit sed diam nonummy nibh euismod tincidunt ut laoreet.</p>
  <div class="foot">© 2017 ALDERFIELD. All rights reserved<b>34</b></div>
</section>

<!-- Line chart slide -->
<section class="slide c2 r1">
  <span class="marker"></span><div class="brand">Alderfield</div>
  <h2 class="abs" style="left:23px;top:52px;font-size:15px;line-height:18px;font-weight:700;color:var(--navy)">This Is Line<br>Chart Slide</h2>
  <div class="abs" style="left:25px;top:102px;width:76px;height:11px;background:var(--sky);color:#fff;font-size:5px;line-height:11px;text-align:center">CREATE TEXT HERE</div>
  <p class="abs small" style="left:25px;top:128px;width:82px;font-size:5px;line-height:6.5px"><span style="color:var(--bright)">Lorem ipsum dolor</span> sit amet, consectetur adipiscing elit, sed do eiusmod tempor incididunt ut labore et commodo consequat dolore magna aliqua.</p>
  <svg class="abs" style="left:140px;top:44px" width="196" height="125" viewBox="0 0 196 125">
    <g font-size="4" fill="#999"><text x="0" y="6">5</text><text x="0" y="58">2.5</text><text x="0" y="112">0</text><text x="22" y="122">Category 1</text><text x="66" y="122">Category 2</text><text x="110" y="122">Category 3</text><text x="154" y="122">Category 4</text></g>
    <polyline points="32,24 76,68 120,48 164,18" fill="none" stroke="var(--sky)" stroke-width="1.3"/>
    <polyline points="32,68 76,20 120,84 164,58" fill="none" stroke="var(--teal)" stroke-width="1.3"/>
    <g fill="var(--sky)"><circle cx="32" cy="24" r="1.8"/><circle cx="76" cy="68" r="1.8"/><circle cx="120" cy="48" r="1.8"/><circle cx="164" cy="18" r="1.8"/></g>
    <g fill="var(--teal)"><circle cx="32" cy="68" r="1.8"/><circle cx="76" cy="20" r="1.8"/><circle cx="120" cy="84" r="1.8"/><circle cx="164" cy="58" r="1.8"/></g>
  </svg>
  <div class="foot">© 2017 ALDERFIELD. All rights reserved<b>35</b></div>
</section>

<!-- Table -->
<section class="slide c3 r1">
  <span class="marker"></span><h2 class="title">Your Table Area</h2><div class="brand">Alderfield</div>
  <p class="abs tiny" style="left:26px;top:48px;width:210px">Description: There are many variations of passages of lorem ipsum available but the majority have suffered alteration.</p>
  <svg class="abs" style="left:22px;top:62px" width="316" height="114" viewBox="0 0 316 114" font-size="4.2" fill="#888">
    <rect x="0" y="0" width="316" height="9" fill="var(--sky)"/>
    <g fill="#fff"><text x="18" y="6">Lorem ipsum</text><text x="86" y="6">Value</text><text x="146" y="6">Value</text><text x="206" y="6">Value</text><text x="266" y="6">Value</text></g>
    <g fill="#f3f5f6"><rect y="9" width="316" height="10.5"/><rect y="30" width="316" height="10.5"/><rect y="51" width="316" height="10.5"/><rect y="72" width="316" height="10.5"/><rect y="93" width="316" height="10.5"/></g>
    <g><text x="18" y="16">Lorem ipsum</text><text x="86" y="16">10</text><text x="146" y="16">15</text><text x="206" y="16">16</text><text x="266" y="16">18</text>
    <text x="18" y="26">Lorem ipsum</text><text x="86" y="26">12</text><text x="146" y="26">13</text><text x="206" y="26">15</text><text x="266" y="26">16</text>
    <text x="18" y="37">Lorem ipsum</text><text x="86" y="37">20</text><text x="146" y="37">22</text><text x="206" y="37">21</text><text x="266" y="37">21</text>
    <text x="18" y="47">Lorem ipsum</text><text x="86" y="47">10</text><text x="146" y="47">21</text><text x="206" y="47">12</text><text x="266" y="47">11</text>
    <text x="18" y="58">Lorem ipsum</text><text x="86" y="58">25</text><text x="146" y="58">25</text><text x="206" y="58">25</text><text x="266" y="58">25</text>
    <text x="18" y="68">Lorem ipsum</text><text x="86" y="68">10</text><text x="146" y="68">02</text><text x="206" y="68">51</text><text x="266" y="68">21</text>
    <text x="18" y="79">Lorem ipsum</text><text x="86" y="79">35</text><text x="146" y="79">35</text><text x="206" y="79">65</text><text x="266" y="79">32</text>
    <text x="18" y="89">Lorem ipsum</text><text x="86" y="89">26</text><text x="146" y="89">33</text><text x="206" y="89">35</text><text x="266" y="89">32</text>
    <text x="18" y="100">Lorem ipsum</text><text x="86" y="100">32</text><text x="146" y="100">10</text><text x="206" y="100">32</text><text x="266" y="100">32</text></g>
  </svg>
  <div class="foot">© 2017 ALDERFIELD. All rights reserved<b>36</b></div>
</section>

<!-- Blank -->
<section class="slide c1 r2">
  <div class="abs" style="left:0;top:0;width:342px;height:32px;background:var(--blue)"></div>
  <span class="marker" style="border-left-color:#dfe9ef"></span>
  <h2 class="title" style="left:18px;top:9px;color:#fff">Your Blank Slide</h2>
  <div class="brand" style="color:#fff;top:7px">Alderfield</div>
  <div class="foot">© 2017 ALDERFIELD. All rights reserved<b>37</b></div>
</section>

<!-- Subscription -->
<section class="slide c2 r2">
  <span class="marker"></span><h2 class="title ul">Monthly Subscription</h2><div class="brand">Alderfield</div>
  <div class="abs" style="left:0;top:96px;width:342px;height:96px;background:var(--blue)"></div>
  <div class="abs" style="left:50px;top:64px;width:68px;height:93px;background:#fff"></div>
  <div class="abs" style="left:50px;top:64px;width:68px;height:31px;background:var(--sky);color:#fff;text-align:center;font-size:13px;line-height:31px">$300</div>
  <div class="abs" style="left:126px;top:60px;width:87px;height:104px;background:#fff"></div>
  <div class="abs" style="left:126px;top:60px;width:87px;height:35px;background:var(--deep);color:#fff;text-align:center;font-size:15px;line-height:35px">$900</div>
  <div class="abs" style="left:223px;top:64px;width:68px;height:93px;background:#fff"></div>
  <div class="abs" style="left:223px;top:64px;width:68px;height:31px;background:var(--teal);color:#fff;text-align:center;font-size:13px;line-height:31px">$400</div>
  <div class="abs tiny" style="left:50px;top:100px;width:68px;text-align:center;line-height:12.5px">Single Edition<br>20gb Cloud Service<br>3 User<br>Free Update</div>
  <div class="abs tiny" style="left:126px;top:101px;width:87px;text-align:center;line-height:13.5px">Business Edition<br>60gb Cloud Service<br>6 User<br>Free Update</div>
  <div class="abs tiny" style="left:223px;top:100px;width:68px;text-align:center;line-height:12.5px">Single Edition<br>20gb Cloud Service<br>3 User<br>Free Update</div>
</section>

<!-- Divider -->
<section class="slide c3 r2">
  <div class="ph" role="img" aria-label="Soft blue background of glass office towers" style="inset:0;background:linear-gradient(120deg,#9ec8dc,#6fa9c6 55%,#8dbfd6)"></div>
  <div class="brand" style="top:20px;right:20px;font-size:28px;color:var(--deep)">Alderfield</div>
  <div class="abs" style="left:0;top:98px;width:200px;text-align:center;color:#fff">
    <div style="font-size:5.5px">Divider Page</div>
    <div style="font-size:15px;font-weight:600;margin-top:1px">Your Title Goes Here</div>
    <div style="font-size:8px;opacity:.8">Your Subtitle Here</div>
  </div>
</section>

<!-- Mock up -->
<section class="slide c1 r3">
  <div class="abs" style="left:0;top:0;width:342px;height:118px;background:var(--blue)"></div>
  <h2 class="abs" style="left:15px;top:42px;width:100px;text-align:center;color:#fff;font-size:15px;line-height:20px;font-weight:600">Our Mock<br>Up Area</h2>
  <div class="ph" role="img" aria-label="Laptop mockup showing the brand name on screen" style="left:110px;top:30px;width:160px;height:97px;background:linear-gradient(#dfe3e6,#c2c8cc);border-radius:4px 4px 1px 1px"></div>
  <div class="abs" style="left:119px;top:37px;width:142px;height:80px;background:var(--teal);color:var(--navy);font-size:15px;text-align:center;line-height:80px">Alderfield</div>
  <div class="abs tiny" style="left:14px;top:133px;width:84px;text-align:right"><span class="lbl" style="font-weight:500;font-size:5.5px">Your Text Here</span><br>Lorem ipsum dolor sit amet</div>
  <div class="abs tiny" style="left:14px;top:157px;width:84px;text-align:right"><span class="lbl" style="font-weight:500;font-size:5.5px">Your Text Here</span><br>Lorem ipsum dolor sit amet</div>
  <div class="abs circle" style="left:101px;top:134px;width:9px;height:9px;background:var(--sky)"></div>
  <div class="abs circle" style="left:101px;top:157px;width:9px;height:9px;background:var(--sky)"></div>
  <div class="abs circle" style="left:244px;top:136px;width:9px;height:9px;background:var(--sky)"></div>
  <div class="abs circle" style="left:244px;top:159px;width:9px;height:9px;background:var(--sky)"></div>
  <div class="abs tiny" style="left:258px;top:135px;width:84px"><span class="lbl" style="font-weight:500;font-size:5.5px">Your Text Here</span><br>Lorem ipsum dolor sit amet</div>
  <div class="abs tiny" style="left:258px;top:158px;width:84px"><span class="lbl" style="font-weight:500;font-size:5.5px">Your Text Here</span><br>Lorem ipsum dolor sit amet</div>
  <div class="foot">© 2017 ALDERFIELD. All rights reserved<b>40</b></div>
</section>

<!-- Video -->
<section class="slide c2 r3">
  <span class="marker"></span><div class="brand">Alderfield</div>
  <h2 class="abs" style="left:15px;top:28px;font-size:14px;line-height:15px;font-weight:700;color:var(--navy)">Video Title<br>Goes Here</h2>
  <div class="abs" style="left:15px;top:59px;width:22px;height:2px;background:var(--teal)"></div>
  <p class="abs tiny" style="left:15px;top:78px;width:80px">Lorem ipsum dolor sit amet, consectetur adipiscing elit, sed do eiusmod tempor incididunt ut labore et commodo consequat dolore magna aliqua.<br><br>Duis aute irure dolor in reprehenderit in voluptate velit esse cillum dolore eu fugiat nulla pariatur.<br><br>Ut enimad minim veniam, quis nostrud exercitation ullamco laboris.</p>
  <div class="abs" style="left:107px;top:30px;width:191px;height:120px;background:#2b2f33;border-radius:4px"></div>
  <div class="ph" role="img" aria-label="Video still of a business meeting with documents" style="left:112px;top:35px;width:181px;height:108px;background:linear-gradient(135deg,#e9edf0,#aab5be)"></div>
  <div class="abs" style="left:185px;top:150px;width:35px;height:12px;background:#d6dade"></div>
  <div class="foot">© 2017 ALDERFIELD. All rights reserved<b>41</b></div>
</section>

<!-- Four column boxes -->
<section class="slide c3 r3">
  <span class="marker"></span><h2 class="title ul">Four Column Area</h2><div class="brand">Alderfield</div>
  <p class="abs tiny" style="left:28px;top:52px;width:290px;text-align:center">Lorem ipsum dolor sit amet, consectetur adipiscing elit, sed do eiusmod tempor incididunt ut labore et dolore magna aliqua. Ut enimad minim veniam, quis nostrud exercitation ullamco laboris nisi ut aliquip ex ea commodo consequat.</p>
  <div class="abs" style="left:27px;top:72px;width:63px;height:84px;background:var(--blue)"></div>
  <div class="abs" style="left:102px;top:72px;width:63px;height:84px;background:var(--teal)"></div>
  <div class="abs" style="left:177px;top:72px;width:63px;height:84px;background:var(--blue)"></div>
  <div class="abs" style="left:252px;top:72px;width:63px;height:84px;background:var(--teal)"></div>
  <div class="abs circle" style="left:50px;top:84px;width:17px;height:17px;border:2px solid #fff"></div>
  <div class="abs circle" style="left:125px;top:84px;width:17px;height:17px;border:2px solid #fff"></div>
  <div class="abs circle" style="left:200px;top:84px;width:17px;height:17px;border:2px solid #fff"></div>
  <div class="abs circle" style="left:275px;top:84px;width:17px;height:17px;border:2px solid #fff"></div>
  <div class="abs tiny" style="left:27px;top:118px;width:63px;text-align:center;color:#fff">YOUR TEXT HERE<br>Lorem ipsum dolor sit consectetur adipiscing elit.</div>
  <div class="abs tiny" style="left:102px;top:118px;width:63px;text-align:center;color:#fff">YOUR TEXT HERE<br>Lorem ipsum dolor sit consectetur adipiscing elit.</div>
  <div class="abs tiny" style="left:177px;top:118px;width:63px;text-align:center;color:#fff">YOUR TEXT HERE<br>Lorem ipsum dolor sit consectetur adipiscing elit.</div>
  <div class="abs tiny" style="left:252px;top:118px;width:63px;text-align:center;color:#fff">YOUR TEXT HERE<br>Lorem ipsum dolor sit consectetur adipiscing elit.</div>
  <div class="foot">© 2017 ALDERFIELD. All rights reserved<b>42</b></div>
</section>

<!-- Four column circles -->
<section class="slide c1 r4">
  <span class="marker"></span><h2 class="title ul">Four Column Area</h2><div class="brand">Alderfield</div>
  <p class="abs tiny" style="left:40px;top:45px;width:262px;text-align:center">Lorem ipsum dolor sit amet, consectetur adipiscing elit, sed do eiusmod tempor incididunt ut labore et dolore magna aliqua. Ut enimad minim veniam, quis nostrud exercitation ullamco laboris nisi ut aliquip ex ea commodo consequat.</p>
  <svg class="abs" style="left:0;top:66px" width="342" height="46" viewBox="0 0 342 46">
    <circle cx="68" cy="22" r="20" fill="none" stroke="var(--bright)" stroke-width="2.5"/><circle cx="68" cy="22" r="14" fill="#fff" stroke="var(--sky)" stroke-width=".8"/>
    <circle cx="137" cy="22" r="20" fill="none" stroke="var(--sky)" stroke-width="2.5"/><circle cx="137" cy="22" r="15" fill="var(--sky)"/>
    <circle cx="206" cy="22" r="20" fill="none" stroke="var(--teal)" stroke-width="2.5"/><circle cx="206" cy="22" r="15" fill="var(--teal)"/>
    <circle cx="274" cy="22" r="20" fill="none" stroke="var(--grey)" stroke-width="2.5"/><circle cx="274" cy="22" r="14" fill="#fff" stroke="var(--grey)" stroke-width=".8"/>
    <circle cx="274" cy="22" r="4" fill="var(--grey)"/><path d="M63 17h10l-2 6h-6z M66 23v5h4" fill="none" stroke="var(--bright)" stroke-width="1.2"/>
    <path d="M131 25l1-7 5 4 5-4 1 7z" fill="#fff"/><path d="M201 27l9-9M204 18h6v6" fill="none" stroke="#fff" stroke-width="1.4"/>
  </svg>
  <div class="abs" style="left:0;top:114px;width:342px;font-size:5.5px;font-weight:700;color:#333">
    <span class="abs" style="left:48px;width:40px;text-align:center">COLUMN 1</span><span class="abs" style="left:117px;width:40px;text-align:center">COLUMN 2</span><span class="abs" style="left:186px;width:40px;text-align:center">COLUMN 3</span><span class="abs" style="left:254px;width:40px;text-align:center">COLUMN 4</span>
  </div>
  <p class="abs tiny" style="left:40px;top:124px;width:56px;text-align:center">Lorem ipsum dolor sit amet, consectetur adipiscing elit, sed do eiusmod tempor incididunt.</p>
  <p class="abs tiny" style="left:109px;top:124px;width:56px;text-align:center">Lorem ipsum dolor sit amet, consectetur adipiscing elit, sed do eiusmod tempor incididunt.</p>
  <p class="abs tiny" style="left:178px;top:124px;width:56px;text-align:center">Lorem ipsum dolor sit amet, consectetur adipiscing elit, sed do eiusmod tempor incididunt.</p>
  <p class="abs tiny" style="left:246px;top:124px;width:56px;text-align:center">Lorem ipsum dolor sit amet, consectetur adipiscing elit, sed do eiusmod tempor incididunt.</p>
  <div class="foot">© 2017 ALDERFIELD. All rights reserved<b>43</b></div>
</section>

<!-- Key points -->
<section class="slide c2 r4">
  <span class="marker"></span><h2 class="title ul">Key Points Area</h2><div class="brand">Alderfield</div>
  <p class="abs tiny" style="left:20px;top:56px;width:300px">Lorem ipsum dolor sit amet, consectetur adipiscing elit, sed do eiusmod tempor incididunt ut labore et dolore magna aliqua. Ut enimad minim veniam, quis nostrud exercitation ullamco laboris nisi ut aliquip ex ea commodo consequat.</p>
  <svg class="abs" style="left:60px;top:84px" width="230" height="50" viewBox="0 0 230 50">
    <circle cx="27" cy="24" r="22.5" fill="var(--blue)"/><circle cx="67" cy="24" r="22.5" fill="var(--teal)" opacity=".95"/>
    <circle cx="107" cy="24" r="22.5" fill="var(--grey)" opacity=".95"/><circle cx="147" cy="24" r="22.5" fill="var(--teal)" opacity=".95"/>
    <circle cx="187" cy="24" r="22.5" fill="var(--blue)" opacity=".95"/>
    <g fill="#fff" font-size="4.2" text-anchor="middle"><text x="27" y="30">Lorem</text><text x="27" y="35">ipsum</text><text x="67" y="30">Lorem</text><text x="67" y="35">ipsum</text><text x="107" y="30">Lorem</text><text x="107" y="35">ipsum</text><text x="147" y="30">Lorem</text><text x="147" y="35">ipsum</text><text x="187" y="30">Lorem</text><text x="187" y="35">ipsum</text></g>
    <g fill="#fff"><circle cx="27" cy="19" r="3"/><rect x="64" y="16" width="6" height="6"/><rect x="104" y="17" width="2" height="5"/><rect x="108" y="15" width="2" height="7"/><circle cx="147" cy="19" r="3"/><rect x="184" y="16" width="6" height="5"/></g>
  </svg>
  <p class="abs tiny" style="left:62px;top:142px;width:218px;text-align:center">Lorem ipsum dolor sit amet, consectetur adipiscing elit, sed do eiusmod tempor incididunt ut labore et dolore magna aliqua. Ut enimad minim veniam, quis nostrud exercitation ullamco laboris nisi ut aliquip ex ea commodo consequat.</p>
  <div class="foot">© 2017 ALDERFIELD. All rights reserved<b>44</b></div>
</section>

<!-- Workflow -->
<section class="slide c3 r4">
  <span class="marker"></span><h2 class="title ul">Workflow Area</h2><div class="brand">Alderfield</div>
  <p class="abs tiny" style="left:26px;top:52px;width:295px">Lorem ipsum dolor sit amet, consectetur adipiscing elit, sed do eiusmod tempor incididunt ut labore et dolore magna aliqua. Ut enimad minim veniam, quis nostrud exercitation ullamco laboris nisi ut aliquip ex ea commodo consequat.</p>
  <svg class="abs" style="left:22px;top:82px" width="310" height="70" viewBox="0 0 310 70" fill="none" stroke-width="8">
    <path d="M4 48 A28 28 0 0 1 60 48" stroke="var(--blue)"/>
    <path d="M60 30 A28 28 0 0 0 116 30" stroke="var(--teal)"/>
    <path d="M116 48 A28 28 0 0 1 172 48" stroke="var(--blue)"/>
    <path d="M172 30 A28 28 0 0 0 228 30" stroke="var(--teal)"/>
    <path d="M228 48 A28 28 0 0 1 284 48" stroke="var(--blue)"/>
    <g stroke="none"><circle cx="32" cy="30" r="5" fill="var(--bright)"/><circle cx="88" cy="48" r="5" fill="var(--teal)"/><circle cx="144" cy="30" r="5" fill="var(--bright)"/><circle cx="200" cy="48" r="5" fill="var(--teal)"/><circle cx="256" cy="30" r="5" fill="var(--bright)"/></g>
    <g stroke="none" font-size="5.5" font-weight="600"><text x="24" y="44" fill="var(--bright)">Data 1</text><text x="80" y="9" fill="var(--teal)">Data 2</text><text x="136" y="44" fill="var(--bright)">Data 3</text><text x="192" y="9" fill="var(--teal)">Data 4</text><text x="248" y="44" fill="var(--bright)">Data 5</text></g>
  </svg>
  <p class="abs tiny" style="left:46px;top:132px;width:40px;text-align:center">Lorem ipsum dolor sit amet, consectetur adipiscing elit.</p>
  <p class="abs tiny" style="left:158px;top:132px;width:40px;text-align:center">Lorem ipsum dolor sit amet, consectetur adipiscing elit.</p>
  <p class="abs tiny" style="left:270px;top:132px;width:40px;text-align:center">Lorem ipsum dolor sit amet, consectetur adipiscing elit.</p>
  <p class="abs tiny" style="left:102px;top:96px;width:40px;text-align:center">Lorem ipsum dolor sit amet, consectetur adipiscing elit.</p>
  <p class="abs tiny" style="left:214px;top:96px;width:40px;text-align:center">Lorem ipsum dolor sit amet, consectetur adipiscing elit.</p>
  <div class="foot">© 2017 ALDERFIELD. All rights reserved<b>45</b></div>
</section>

<!-- Timeline -->
<section class="slide c1 r5">
  <span class="marker"></span><h2 class="title ul">Timeline</h2><div class="brand">Alderfield</div>
  <svg class="abs" style="left:25px;top:40px" width="300" height="110" viewBox="0 0 300 110">
    <line x1="22" y1="55" x2="285" y2="55" stroke="#bbb" stroke-width=".8"/>
    <g stroke="#bbb" stroke-width=".8"><line x1="62" y1="36" x2="62" y2="55"/><line x1="144" y1="36" x2="144" y2="55"/><line x1="225" y1="36" x2="225" y2="55"/><line x1="103" y1="55" x2="103" y2="72"/><line x1="184" y1="55" x2="184" y2="72"/></g>
    <circle cx="22" cy="55" r="19" fill="var(--blue)"/><circle cx="62" cy="19" r="19" fill="var(--sky)"/>
    <circle cx="144" cy="19" r="19" fill="var(--grey)"/><circle cx="225" cy="19" r="19" fill="var(--sky)"/>
    <circle cx="103" cy="89" r="19" fill="var(--teal)"/><circle cx="184" cy="89" r="19" fill="var(--teal)"/>
    <circle cx="277" cy="55" r="19" fill="var(--blue)"/>
    <g fill="#fff" font-size="8" text-anchor="middle"><text x="22" y="56">2010</text><text x="62" y="20">2011</text><text x="144" y="20">2013</text><text x="225" y="20">2015</text><text x="103" y="90">2012</text><text x="184" y="90">2014</text><text x="277" y="56">2018</text></g>
    <g fill="#fff" font-size="3.5" text-anchor="middle"><text x="22" y="62">Your Text</text><text x="62" y="26">Your Text</text><text x="144" y="26">Your Text</text><text x="225" y="26">Your Text</text><text x="103" y="96">Your Text</text><text x="184" y="96">Your Text</text><text x="277" y="62">Your Text</text></g>
  </svg>
  <div class="abs tiny" style="left:240px;top:116px;width:90px;text-align:center"><span style="font-size:6px;color:var(--navy)">Your Text Goes Here</span><br>Lorem ipsum dolor sit amet, consectetur adipiscing elit, sed do.</div>
  <div class="abs tiny" style="left:18px;top:150px;width:150px"><span style="font-size:6px;color:var(--navy)">Your Text Goes Here</span><br>Lorem ipsum dolor sit amet, consectetur adipiscing elit, sed do eiusmod tempor incididunt.</div>
  <div class="foot">© 2017 ALDERFIELD. All rights reserved<b>46</b></div>
</section>

<!-- Team -->
<section class="slide c2 r5">
  <span class="marker"></span><h2 class="title ul">Our Team</h2><div class="brand">Alderfield</div>
  <div class="ph circle" role="img" aria-label="Portrait of Michael Doe" style="left:23px;top:47px;width:37px;height:37px"></div>
  <div class="ph circle" role="img" aria-label="Portrait of James Doe" style="left:173px;top:47px;width:37px;height:37px"></div>
  <div class="ph circle" role="img" aria-label="Portrait of Jane Doe" style="left:23px;top:111px;width:37px;height:37px"></div>
  <div class="ph circle" role="img" aria-label="Portrait of John Doe" style="left:173px;top:111px;width:37px;height:37px"></div>
  <div class="abs tiny" style="left:64px;top:54px;width:100px"><b style="font-size:6px;color:#333">Michael Doe</b><br>CEO<br>MSMPT, MBA and CMA Dip PM<br>• Lorem ipsum dolor sit amet, consectetur<br>• sed do eiusmod tempor incididunt ut labore<br>• Ut enimad minim veniam, quis nostrud</div>
  <div class="abs tiny" style="left:214px;top:54px;width:100px"><b style="font-size:6px;color:#333">James Doe</b><br>MANAGER<br>M.B.A<br>• Lorem ipsum dolor sit amet, consectetur<br>• sed do eiusmod tempor incididunt ut labore<br>• Ut enimad minim veniam, quis nostrud</div>
  <div class="abs tiny" style="left:64px;top:118px;width:100px"><b style="font-size:6px;color:#333">Jane Doe</b><br>Doctor of Chemistry<br>M.B.A<br>• Lorem ipsum dolor sit amet, consectetur<br>• sed do eiusmod tempor incididunt ut labore<br>• Ut enimad minim veniam, quis nostrud</div>
  <div class="abs tiny" style="left:214px;top:118px;width:100px"><b style="font-size:6px;color:#333">John Doe</b><br>Doctor of Physical<br>Professor<br>• Lorem ipsum dolor sit amet, consectetur<br>• sed do eiusmod tempor incididunt ut labore<br>• Ut enimad minim veniam, quis nostrud</div>
  <div class="foot">© 2017 ALDERFIELD. All rights reserved<b>47</b></div>
</section>

<!-- Testimonials -->
<section class="slide c3 r5">
  <span class="marker"></span><h2 class="title ul">Customer Testimonials</h2><div class="brand">Alderfield</div>
  <div class="abs" style="left:0;top:102px;width:342px;height:90px;background:var(--blue)"></div>
  <div class="ph circle" role="img" aria-label="Portrait of a satisfied client" style="left:74px;top:42px;width:47px;height:47px;border:2px solid #fff"></div>
  <p class="abs tiny" style="left:146px;top:54px;width:150px">adipiscing elit, sed diam nonummy nibh euismod tincidunt ut laoreet dolore magna aliquam erat volutpat. Ut wisi enim <b style="color:var(--navy)">Lorem Ipsum</b> dolor sit amet, consectetur adipiscing elit, sed diam nonummy nibh euismod tincidunt ut laoreet dolore magna.</p>
  <div class="abs circle" style="left:70px;top:116px;width:26px;height:26px;border:1.2px solid #fff"></div>
  <div class="abs circle" style="left:133px;top:116px;width:26px;height:26px;border:1.2px solid #fff"></div>
  <div class="abs circle" style="left:196px;top:116px;width:26px;height:26px;border:1.2px solid #fff"></div>
  <div class="abs circle" style="left:259px;top:116px;width:26px;height:26px;border:1.2px solid #fff"></div>
  <p class="abs tiny" style="left:58px;top:150px;width:50px;text-align:center;color:#fff">Why does getting a loan have to be so much more complicated?</p>
  <p class="abs tiny" style="left:121px;top:150px;width:50px;text-align:center;color:#fff">Why do I have to go to a branch to fill out forms and wait for weeks?</p>
  <p class="abs tiny" style="left:184px;top:150px;width:50px;text-align:center;color:#fff">Who do banks refuse to lend to me despite my substantial income?</p>
  <p class="abs tiny" style="left:247px;top:150px;width:50px;text-align:center;color:#fff">Why is there no service that identifies my needs and offers convenience?</p>
</section>

<!-- Bullet & bar chart -->
<section class="slide c1 r6">
  <span class="marker"></span><h2 class="title ul">Bullet &amp; Chart Area</h2><div class="brand">Alderfield</div>
  <svg class="abs" style="left:20px;top:58px" width="150" height="108" viewBox="0 0 150 108">
    <g font-size="3.8" fill="#999"><text x="0" y="11">Category 4</text><text x="0" y="36">Category 3</text><text x="0" y="61">Category 2</text><text x="0" y="86">Category 1</text></g>
    <line x1="30" y1="0" x2="30" y2="96" stroke="#ddd" stroke-width=".6"/>
    <rect x="30" y="2" width="94" height="5" fill="var(--sky)"/><rect x="30" y="8" width="40" height="5" fill="var(--teal)"/><rect x="30" y="14" width="64" height="5" fill="var(--grey)"/>
    <rect x="30" y="27" width="56" height="5" fill="var(--sky)"/><rect x="30" y="33" width="34" height="5" fill="var(--teal)"/><rect x="30" y="39" width="66" height="5" fill="var(--grey)"/>
    <rect x="30" y="52" width="44" height="5" fill="var(--sky)"/><rect x="30" y="58" width="72" height="5" fill="var(--teal)"/><rect x="30" y="64" width="58" height="5" fill="var(--grey)"/>
    <rect x="30" y="77" width="47" height="5" fill="var(--sky)"/><rect x="30" y="83" width="24" height="5" fill="var(--teal)"/><rect x="30" y="89" width="78" height="5" fill="var(--grey)"/>
    <g font-size="3.5" fill="#999"><rect x="48" y="102" width="3" height="3" fill="var(--sky)"/><text x="53" y="105">Series 3</text><rect x="72" y="102" width="3" height="3" fill="var(--teal)"/><text x="77" y="105">Series 2</text><rect x="96" y="102" width="3" height="3" fill="var(--grey)"/><text x="101" y="105">Series 1</text></g>
  </svg>
  <div class="abs circle" style="left:197px;top:70px;width:12px;height:12px;background:var(--sky)"></div>
  <div class="abs circle" style="left:197px;top:98px;width:12px;height:12px;background:var(--sky)"></div>
  <div class="abs circle" style="left:197px;top:125px;width:12px;height:12px;background:var(--sky)"></div>
  <div class="abs circle" style="left:197px;top:153px;width:12px;height:12px;background:var(--sky)"></div>
  <div class="abs tiny" style="left:216px;top:69px;width:110px"><span class="lbl" style="font-weight:500">Category One</span><br>Lorem ipsum dolor sit amet, consectetur adipiscing elit, sed do eiusmod.</div>
  <div class="abs tiny" style="left:216px;top:97px;width:110px"><span class="lbl" style="font-weight:500">Category Two</span><br>Lorem ipsum dolor sit amet, consectetur adipiscing elit, sed do eiusmod.</div>
  <div class="abs tiny" style="left:216px;top:124px;width:110px"><span class="lbl" style="font-weight:500">Category Three</span><br>Lorem ipsum dolor sit amet, consectetur adipiscing elit, sed do eiusmod.</div>
  <div class="abs tiny" style="left:216px;top:152px;width:110px"><span class="lbl" style="font-weight:500">Category Four</span><br>Lorem ipsum dolor sit amet, consectetur adipiscing elit, sed do eiusmod.</div>
  <div class="foot">© 2017 ALDERFIELD. All rights reserved<b>49</b></div>
</section>

<!-- Bullet & donut -->
<section class="slide c2 r6">
  <span class="marker"></span><h2 class="title ul">Bullet &amp; Chart Area</h2><div class="brand">Alderfield</div>
  <div class="abs circle" style="left:34px;top:63px;width:12px;height:12px;background:var(--sky)"></div>
  <div class="abs circle" style="left:34px;top:91px;width:12px;height:12px;background:var(--teal)"></div>
  <div class="abs circle" style="left:34px;top:119px;width:12px;height:12px;background:var(--sky)"></div>
  <div class="abs circle" style="left:34px;top:146px;width:12px;height:12px;background:var(--grey)"></div>
  <div class="abs tiny" style="left:56px;top:62px;width:100px"><span style="font-size:6px;color:var(--sky)">Your Text Here</span><br>Lorem ipsum dolor sit amet, consectetur adipiscing elit, sed do eiusmod.</div>
  <div class="abs tiny" style="left:56px;top:90px;width:100px"><span style="font-size:6px;color:var(--sky)">Your Text Here</span><br>Lorem ipsum dolor sit amet, consectetur adipiscing elit, sed do eiusmod.</div>
  <div class="abs tiny" style="left:56px;top:118px;width:100px"><span style="font-size:6px;color:var(--sky)">Your Text Here</span><br>Lorem ipsum dolor sit amet, consectetur adipiscing elit, sed do eiusmod.</div>
  <div class="abs tiny" style="left:56px;top:145px;width:100px"><span style="font-size:6px;color:var(--sky)">Your Text Here</span><br>Lorem ipsum dolor sit amet, consectetur adipiscing elit, sed do eiusmod.</div>
  <svg class="abs" style="left:180px;top:54px" width="160" height="120" viewBox="0 0 160 120">
    <g transform="translate(80,56)" fill="none" stroke-width="9">
      <circle r="28" stroke="var(--blue)" stroke-dasharray="105.6 176" transform="rotate(-90)"/>
      <circle r="28" stroke="var(--teal)" stroke-dasharray="44 176" stroke-dashoffset="-105.6" transform="rotate(-90)"/>
      <circle r="28" stroke="var(--sky)" stroke-dasharray="26.4 176" stroke-dashoffset="-149.6" transform="rotate(-90)"/>
      <circle r="28" stroke="var(--grey)" stroke-dasharray="17.6 176" stroke-dashoffset="-176" transform="rotate(-90)"/>
      <g stroke="none" fill="var(--blue)"><rect x="-7" y="2" width="3" height="6"/><rect x="-2" y="-3" width="3" height="11"/><rect x="3" y="-8" width="3" height="16"/></g>
    </g>
    <g font-size="10" fill="var(--teal)"><text x="54" y="14" fill="var(--grey)">10%</text><text x="10" y="46" fill="var(--sky)">15%</text><text x="10" y="96">25%</text><text x="128" y="64" fill="var(--blue)">60%</text></g>
    <g font-size="3.5" fill="#999"><circle cx="40" cy="116" r="1.2" fill="var(--blue)"/><text x="43" y="117">1st Qtr</text><circle cx="60" cy="116" r="1.2" fill="var(--teal)"/><text x="63" y="117">2nd Qtr</text><circle cx="82" cy="116" r="1.2" fill="var(--sky)"/><text x="85" y="117">3rd Qtr</text><circle cx="102" cy="116" r="1.2" fill="var(--grey)"/><text x="105" y="117">4th Qtr</text></g>
  </svg>
  <div class="foot">© 2017 ALDERFIELD. All rights reserved<b>50</b></div>
</section>

<!-- Contact -->
<section class="slide c3 r6">
  <div class="ph" role="img" aria-label="Soft teal background of a businessman in an office" style="inset:0;background:linear-gradient(120deg,#9bcfd0,#86c4c8 55%,#a8d4d3)"></div>
  <div class="abs" style="left:32px;top:0;width:121px;height:192px;background:rgba(122,184,216,.88)"></div>
  <div class="abs" style="left:34px;top:175px;width:117px;height:17px;background:var(--deep)"></div>
  <div class="brand" style="left:55px;right:auto;top:15px;font-size:20px;color:var(--deep)">Alderfield</div>
  <div class="abs" style="left:46px;top:66px;color:#fff;font-size:14px;font-weight:600">Our Contact</div>
  <div class="abs" style="left:46px;top:85px;width:40px;height:1px;background:#fff"></div>
  <div class="abs tiny" style="left:56px;top:97px;color:#fff;font-size:5px;line-height:7px">123 Street Road<br>City 12345</div>
  <div class="abs tiny" style="left:56px;top:116px;color:#fff;font-size:5px">(123) 456-7890</div>
  <div class="abs tiny" style="left:56px;top:132px;color:#fff;font-size:5px">emailaddress@email.com</div>
  <div class="abs tiny" style="left:56px;top:147px;color:#fff;font-size:5px">www.website-address.com</div>
  <svg class="abs" style="left:44px;top:97px" width="8" height="58" viewBox="0 0 8 58" fill="#fff">
    <path d="M1 4 L4 1 L7 4 V7 H1Z"/><path d="M2 20c1 3 3 5 5 5l0-2-2-1-1 1c-1-1-1-1-1-2l1-1-1-2z"/><rect x="1" y="35" width="6" height="4"/><circle cx="4" cy="52" r="3"/>
  </svg>
  <div class="abs circle" style="left:79px;top:180px;width:7px;height:7px;background:#fff"></div>
  <div class="abs circle" style="left:90px;top:180px;width:7px;height:7px;background:#fff"></div>
  <div class="abs circle" style="left:101px;top:180px;width:7px;height:7px;background:#fff"></div>
  <div class="abs" style="left:196px;top:111px;width:132px;text-align:center;color:#fff">
    <div style="font-size:15px;font-weight:600">THANK YOU</div>
    <div style="font-size:6px">For Your Precious Time</div>
    <div style="font-size:5px;margin-top:5px;line-height:7px">Stop by our office or give us a call!<br>We would love to hear from you.</div>
  </div>
</section>

</div>
</body>
</html>
```